Briloran Clear Springs needs a new business card design (we produce and sell pure bottled water)

We need a clean modern design for our new business cards, We have an existing logo which ultimately cannot be changed, however it could be slighty improved and the colours adjusted. We have this existing logo on all of our bottles, vehicles etc.

Our company slogan is "Pure down to the last drop".
Along with our relevant company information
(Address, phone, website email etc) we will only be using names and not putting position titles for flexibilty.

We are looking for a clean, minimalist modern design.

You can view our website (if need of an update also!) to see our business.

Industry/Entity Type

Business

Contact Information for Business Card

Staff Name : XXXXXX XXXXXX
Address : 9/41 Tavenor St
Halden Rise QLD 4172
Staff Mobile Number : 04XX XXX XXX
Office Phone Number : 07 3918 2457
Staff Email Address : XXXX@brilorancleargo.com.au
Website : www.brilorancleargo.com.au

Font styles to use
Sans Serif

Colors
cee9f5
33a6d7
0492cd
0455a3
3276b5
85abd2
cedeed

Requirements
Must have
• The ability to edit and change the staff members details as we will need to edit for each respective staff member (7 in total)

```html
<!DOCTYPE html>
<html lang="en">
<head>
<meta charset="utf-8">
<title>Briloran Clear Springs — Business Card</title>
<link rel="stylesheet" href="https://fonts.googleapis.com/css2?family=Open+Sans:ital,wght@0,400;0,600;0,700;1,400&display=swap">
<style>
  :root {
    --brand-blue: #33359a;
    --card-white: #ffffff;
    --ink: #1c1c1c;
    --page: #eceef1;
    --card-shadow: rgba(20, 24, 60, 0.18);
  }
  * { box-sizing: border-box; margin: 0; padding: 0; }
  html, body {
    width: 1200px; height: 1200px; overflow: hidden;
    background: var(--page);
  }
  .sheet {
    width: 1200px; height: 1200px;
    display: flex; flex-direction: column; align-items: center; justify-content: center;
    gap: 60px;
  }
  .card {
    position: relative;
    width: 840px; height: 480px;
    background: var(--card-white);
    box-shadow: 0 10px 30px var(--card-shadow);
    overflow: hidden;
    font-family: 'Open Sans', sans-serif;
  }

  /* ---------- Front ---------- */
  .front__band {
    position: absolute; left: 0; top: 0; bottom: 0; width: 112px;
    background: var(--brand-blue);
  }
  .front__edge {
    position: absolute; left: 0; right: 0; top: 0; height: 12px;
    background: var(--brand-blue);
  }
  .brand-mark {
    position: absolute; left: 40px; top: 300px;
    display: flex; align-items: center; gap: 10px;
    background: var(--card-white);
    padding: 12px 16px;
  }
  .brand-mark__dot {
    width: 18px; height: 18px; border-radius: 50%; flex: none;
    background: var(--brand-blue);
  }
  .brand-mark__name {
    font-family: 'Open Sans', sans-serif; font-weight: 700;
    font-size: 20px; letter-spacing: 0.5px; text-transform: uppercase;
    color: var(--brand-blue); line-height: 1.15;
  }
  .staff {
    position: absolute; left: 170px; right: 50px; top: 120px;
    display: flex; align-items: flex-end; gap: 14px;
  }
  .staff__name {
    font-size: 26px; font-weight: 600; color: var(--brand-blue); line-height: 1;
    white-space: nowrap;
  }
  .staff__rule {
    flex: 1; height: 1px; background: var(--brand-blue); margin-bottom: 5px;
  }
  .contact {
    position: absolute; right: 50px; top: 160px;
    list-style: none;
    display: flex; flex-direction: column; align-items: flex-end; gap: 12px;
  }
  .contact__item {
    display: flex; align-items: center; gap: 12px;
    font-size: 18px; color: var(--ink); white-space: nowrap;
  }
  .contact__icon {
    width: 22px; height: 22px; flex: none;
    background: var(--brand-blue);
    display: flex; align-items: center; justify-content: center;
  }
  .contact__icon svg { width: 15px; height: 15px; }

  /* ---------- Back ---------- */
  .back__mark {
    position: absolute; left: 50%; top: 150px; transform: translateX(-50%);
    display: flex; align-items: center; gap: 16px;
  }
  .back__mark .brand-mark__dot { width: 26px; height: 26px; }
  .back__mark .brand-mark__name { font-size: 40px; white-space: nowrap; }
  .slogan {
    position: absolute; left: 0; right: 0; top: 290px; text-align: center;
    font-style: italic; font-size: 24px; color: var(--ink);
  }
</style>
</head>
<body>
<main class="sheet">

  <section class="card card--front" aria-label="Business card front">
    <div class="front__band"></div>
    <div class="front__edge"></div>

    <div class="brand-mark">
      <span class="brand-mark__dot"></span>
      <span class="brand-mark__name">Briloran<br>Clear Springs</span>
    </div>

    <div class="staff">
      <span class="staff__name">Joel Marsh</span>
      <span class="staff__rule"></span>
    </div>

    <ul class="contact">
      <li class="contact__item">07 3918 2457
        <span class="contact__icon">
          <svg viewBox="0 0 16 16" fill="#fff"><path d="M4 1.5l2.2 3-1.3 1.4c.8 1.8 2.2 3.2 4 4l1.4-1.3 3 2.2-1.2 2.4C7 13 3 9 2.8 2.7z"/></svg>
        </span>
      </li>
      <li class="contact__item">XXXX@brilorancleargo.com.au
        <span class="contact__icon">
          <svg viewBox="0 0 16 16" fill="none" stroke="#fff" stroke-width="1.5"><rect x="2" y="4" width="12" height="8"/><path d="M2 4l6 5 6-5"/></svg>
        </span>
      </li>
      <li class="contact__item">www.brilorancleargo.com.au
        <span class="contact__icon">
          <svg viewBox="0 0 16 16" fill="none" stroke="#fff" stroke-width="1.3"><circle cx="8" cy="8" r="6"/><path d="M2 8h12M8 2c-3 3-3 9 0 12M8 2c3 3 3 9 0 12"/></svg>
        </span>
      </li>
      <li class="contact__item">9/41 Tavenor St Halden Rise QLD 4172
        <span class="contact__icon">
          <svg viewBox="0 0 16 16" fill="#fff"><path d="M8 1a4.5 4.5 0 0 0-4.5 4.5C3.5 9 8 15 8 15s4.5-6 4.5-9.5A4.5 4.5 0 0 0 8 1zm0 6.3a1.8 1.8 0 1 1 0-3.6 1.8 1.8 0 0 1 0 3.6z"/></svg>
        </span>
      </li>
    </ul>
  </section>

  <section class="card card--back" aria-label="Business card back">
    <div class="back__mark">
      <span class="brand-mark__dot"></span>
      <span class="brand-mark__name">Briloran Clear Springs</span>
    </div>
    <p class="slogan">"Pure down to the last drop"</p>
  </section>

</main>
</body>
</html>
```